Lucky Harbour Fun Casino Entertainment

Looking to update my business card and make it look more modern, stand out and eye catching.
We are are fun casino business in Australia (primarily Sydney). Blackjack and Roulette are our most popular games although we have pretty much every game available for hire that you would find in a real casino. The final design would need to be sleek and appeal to the more upmarket corporate sector.
We mainly cater for Corporate Events, Private Parties, Fundraising Events, Team Building, Poker Tournaments
I think I'd prefer the colour Black.

Target Market(s)

High-end Corporate

Industry/Entity Type

Events

Contact Information for Business Card

Rob Kendall
Director
1300 482 617
0433 728 591
info@luckyharbour.com.au
www.luckyharbour.com.au
Facebook & Instagram @luckyharbourevents (proper social icons preferred)

Colors
000000
0255a3

Requirements
Must have
• Front side:
• Logo
• Contact details
• 'Sydney's Premier Fun Casino Event Hire'
• Back:
• Logo
Nice to have
• Back:
• Corporate Events
• Private Parties
• Poker Tournaments
• Fundraising
• Props & Theming
• Photo Booth
• Horse Racing Events
• The Vegas Sign attached, maybe on the back of the card in the background...?

```html
<!DOCTYPE html>
<html lang="en">
<head>
<meta charset="utf-8">
<title>Lucky Harbour Business Card</title>
<link href="https://fonts.googleapis.com/css2?family=Open+Sans:wght@400;600;700&display=swap" rel="stylesheet">
<style>
  :root {
    --backdrop: #2b2b2d;
    --card-top: #262626;
    --card-bottom: #0b0b0b;
    --gold: #f7a823;
    --text-light: #e6e6e6;
    --text-muted: #b5b5b5;
    --icon-ink: #111111;
  }
  * { box-sizing: border-box; margin: 0; padding: 0; }
  html, body {
    width: 1200px; height: 844px; overflow: hidden;
    background: var(--backdrop);
    font-family: "Open Sans", Arial, sans-serif;
  }
  .stage {
    width: 1200px; height: 844px;
    display: flex; align-items: center; justify-content: center; gap: 40px;
  }
  .card {
    position: relative;
    width: 540px; height: 310px;
    background: linear-gradient(160deg, var(--card-top) 0%, var(--card-bottom) 70%);
    box-shadow: 0 10px 30px rgba(0,0,0,0.5);
    overflow: hidden;
  }
  .brand {
    display: flex; align-items: center; gap: 10px;
    color: var(--gold); font-weight: 700; font-size: 26px;
    text-transform: uppercase; letter-spacing: 0.5px; white-space: nowrap;
  }
  .brand-dot {
    width: 34px; height: 34px; border-radius: 50%;
    background: var(--gold); flex: none;
  }
  .card-front .brand { position: absolute; top: 52px; right: 70px; }
  .person { position: absolute; left: 40px; top: 150px; }
  .person-name { color: var(--gold); font-weight: 700; font-size: 24px; text-transform: uppercase; line-height: 1.1; }
  .person-role { color: var(--text-muted); font-size: 15px; margin-left: 10px; }
  .contact-list { list-style: none; margin-top: 12px; }
  .contact-list li {
    display: flex; align-items: center; gap: 6px;
    color: var(--text-light); font-size: 17px; line-height: 22px; white-space: nowrap;
  }
  .contact-icon { width: 16px; height: 16px; flex: none; }
  .social { position: absolute; right: 36px; top: 160px; text-align: right; }
  .social-icons { display: flex; gap: 6px; justify-content: flex-end; margin-right: 90px; margin-bottom: 28px; }
  .social-dot { width: 16px; height: 16px; border-radius: 50%; background: var(--gold); }
  .social-handle { color: var(--text-light); font-size: 16px; white-space: nowrap; }
  .card-back { display: flex; flex-direction: column; align-items: center; padding-top: 90px; }
  .tagline {
    margin-top: 70px;
    color: var(--gold); font-weight: 600; font-size: 14px;
    text-transform: uppercase; letter-spacing: 0.5px; white-space: nowrap;
  }
</style>
</head>
<body>
<main class="stage">
  <section class="card card-front">
    <div class="brand"><span class="brand-dot"></span>Lucky Harbour</div>
    <div class="person">
      <p class="person-name">Rob Kendall</p>
      <p class="person-role">Director</p>
      <ul class="contact-list">
        <li><svg class="contact-icon" viewBox="0 0 16 16"><circle cx="8" cy="8" r="8" fill="var(--gold)"/><rect x="4" y="6" width="8" height="6" rx="1" fill="var(--icon-ink)"/><path d="M3.5 6 Q8 2.5 12.5 6" stroke="var(--icon-ink)" stroke-width="1.4" fill="none"/></svg>1300 482 617</li>
        <li><svg class="contact-icon" viewBox="0 0 16 16"><circle cx="8" cy="8" r="8" fill="var(--gold)"/><rect x="5.5" y="3.5" width="5" height="9" rx="1" fill="var(--icon-ink)"/></svg>0433 728 591</li>
        <li><svg class="contact-icon" viewBox="0 0 16 16"><circle cx="8" cy="8" r="8" fill="var(--gold)"/><rect x="4" y="5" width="8" height="6" fill="var(--icon-ink)"/><path d="M4 5 L8 8.5 L12 5" stroke="var(--gold)" stroke-width="1" fill="none"/></svg>info@luckyharbour.com.au</li>
        <li><svg class="contact-icon" viewBox="0 0 16 16"><circle cx="8" cy="8" r="8" fill="var(--gold)"/><circle cx="8" cy="8" r="4" fill="none" stroke="var(--icon-ink)" stroke-width="1.4"/><path d="M4 8 H12 M8 4 V12" stroke="var(--icon-ink)" stroke-width="1"/></svg>www.luckyharbour.com.au</li>
      </ul>
    </div>
    <div class="social">
      <div class="social-icons"><span class="social-dot"></span><span class="social-dot"></span></div>
      <p class="social-handle">@luckyharbourevents</p>
    </div>
  </section>

  <section class="card card-back">
    <div class="brand"><span class="brand-dot"></span>Lucky Harbour</div>
    <p class="tagline">Sydney's Premier Fun Casino Event Hire</p>
  </section>
</main>
</body>
</html>
```